International Travel Technology R&D business needs a wordpress website

We are a start up team of initially 2 individuals but plan to grow our team quickly, we have deep experience in travel technology. Our goal is to provide next generation technology research and development on behalf of our clients who are leading players in the travel technology industry. Attached our logos.

Target Market(s)

Travel Technology companies

Industry/Entity Type

Travel Industry

Coding

Coded - Design and coding required

Font styles to use
Sans Serif

Requirements
Must have
• Make use of our logo and colour scheme in the attached. Has to have a sense of adventure/ stepping into the unknown but equally must convey a sense of professionalism , we are a safe pair of hands. Sample themes are in the attachment .
Nice to have
• We have identified a theme on skinharbor which we feel would be inspirational. We hahe attached them to help in the design as inspiration.
Should not have
• images of airplanes , hotels etc, we want to project a future image.

```html
<!DOCTYPE html>
<html lang="en">
<head>
<meta charset="utf-8">
<title>Nextway Labs</title>
<link rel="stylesheet" href="https://fonts.googleapis.com/css2?family=Raleway:wght@400;500;600;700&family=Open+Sans:ital,wght@0,400;0,600;1,400&display=swap">
<style>
:root{
  --navy:#0a2a6e;
  --nav-top:#7fb0e4;
  --nav-bot:#4f8fd2;
  --blue-band:#1d4f9f;
  --blue-deep:#0c2f78;
  --accent:#4f8fd2;
  --link:#5a93d4;
  --green:#6fb23f;
  --ink:#1c2a3a;
  --muted:#8a8f96;
  --light:#f0f0f0;
  --footer:#6fa3dc;
  --footer-bar:#86b3e4;
  --white:#fff;
}
*{box-sizing:border-box;margin:0;padding:0}
html,body{width:1200px;height:3158px;overflow:hidden;background:var(--white)}
body{font-family:"Open Sans",Arial,sans-serif;color:var(--ink);position:relative}
section,header,footer,nav{position:absolute;left:0;width:1200px}

/* header */
.site-header{top:0;height:114px}
.brand{position:absolute;left:126px;top:20px;display:flex;align-items:center;gap:12px}
.brand-dot{width:34px;height:34px;border-radius:50%;background:var(--accent)}
.brand-name{font-family:"Raleway",sans-serif;font-weight:700;font-size:30px;color:var(--navy);letter-spacing:1px}

.main-nav{top:114px;height:50px;background:linear-gradient(var(--nav-top),var(--nav-bot));display:flex;padding-left:126px}
.main-nav a{font-family:"Raleway",sans-serif;font-weight:600;font-size:15px;color:var(--white);text-decoration:none;display:flex;align-items:center;justify-content:center;height:50px;border-right:1px solid rgba(255,255,255,.35)}
.main-nav a.active{background:var(--navy)}

/* hero */
.hero{top:164px;height:463px}
.hero-photo{position:absolute;inset:0;background:radial-gradient(circle at 50% 42%,#ffe8a8 0%,#f6a14a 22%,#c9705e 42%,#5a6fa8 70%,#2f4d8e 100%)}
.hero-title{position:absolute;top:166px;width:100%;text-align:center;color:var(--white);font-family:"Raleway",sans-serif;font-weight:500;font-size:42px;letter-spacing:1px}
.hero-sub{position:absolute;top:216px;width:100%;text-align:center;color:var(--white);font-family:"Raleway",sans-serif;font-weight:500;font-size:31px;letter-spacing:1px}
.hero-dots{position:absolute;top:418px;left:0;width:100%;display:flex;justify-content:center;gap:6px}
.hero-dots span{width:20px;height:20px;border-radius:50%;background:var(--white)}
.hero-dots span.on{background:transparent;border:2px solid var(--white)}
.hero-arrow{position:absolute;top:404px;width:30px;height:30px;background:rgba(255,255,255,.25)}

/* about */
.about{top:627px;height:314px;text-align:center;padding-top:90px}
.about h2{font-family:"Raleway",sans-serif;font-weight:500;font-size:28px;color:#222;letter-spacing:.5px}
.about .lead{font-size:14px;color:#777;margin-top:6px}
.about .body{font-size:12.5px;color:#777;line-height:26px;margin:14px auto 0;width:920px}

/* services */
.services{top:941px;height:356px;background:linear-gradient(180deg,var(--blue-deep),var(--blue-band) 60%,#2d64b4)}
.service{position:absolute;top:50px;width:300px;text-align:center;color:var(--white)}
.service svg{display:block;margin:0 auto}
.service h3{font-family:"Raleway",sans-serif;font-weight:500;font-size:20px;margin-top:10px}
.service p{font-size:13px;line-height:22px;color:rgba(255,255,255,.65);margin-top:6px}

/* what we do */
.what{top:1297px;height:412px}
.what-media{position:absolute;left:147px;top:60px;width:400px;height:273px;background:linear-gradient(160deg,#dfe8f3,#9fb6d3 55%,#38424f)}
.what-text{position:absolute;left:594px;top:88px;width:460px}
.what-text h2{font-family:"Raleway",sans-serif;font-weight:500;font-size:27px;color:var(--navy)}
.what-text p{font-size:13px;line-height:21px;color:var(--muted);margin-top:14px}
.btn{display:inline-block;font-family:"Raleway",sans-serif;font-weight:700;font-size:12px;text-decoration:none}
.btn-solid{margin-top:22px;background:var(--accent);color:var(--white);padding:10px 28px;border-radius:2px}

/* technology */
.tech{top:1709px;height:396px}
.tech-panel{position:absolute;left:0;top:0;width:615px;height:396px;background:linear-gradient(120deg,#7cbc48,var(--green))}
.tech-panel h2{position:absolute;left:130px;top:70px;font-family:"Raleway",sans-serif;font-weight:500;font-size:28px;color:var(--white)}
.tech-panel p{position:absolute;left:130px;width:430px;font-size:12.5px;line-height:21px;color:rgba(255,255,255,.85)}
.btn-ghost{position:absolute;left:134px;top:285px;border:2px solid var(--white);color:var(--white);padding:9px 22px}
.tech-photo{position:absolute;left:615px;top:0;width:585px;height:396px;background:linear-gradient(135deg,#cfd8e2,#7c8c9e 50%,#3a4350)}

/* projects */
.projects{top:2105px;height:427px;background:var(--light)}
.section-title{position:absolute;top:44px;width:100%;text-align:center;font-family:"Raleway",sans-serif;font-weight:500;font-size:24px}
.projects .section-title{color:var(--accent)}
.project{position:absolute;top:95px;width:297px}
.project-photo{height:162px;background:linear-gradient(135deg,#c9d3de,#6a7c92 60%,#2f3a48)}
.project h3{font-family:"Raleway",sans-serif;font-weight:600;font-size:16px;color:var(--navy);margin-top:18px}
.project p{font-size:11.5px;line-height:19px;color:var(--muted);margin-top:6px}
.project a{display:block;margin-top:6px;font-family:"Raleway",sans-serif;font-weight:700;font-size:12px;color:var(--link);text-decoration:none}

/* testimonials */
.testimonials{top:2532px;height:339px}
.testimonials .section-title{color:#222;top:40px}
.quote-card{position:absolute;top:104px;width:312px;height:155px;border:1px solid #ddd;border-radius:3px;box-shadow:0 1px 3px rgba(0,0,0,.06)}
.avatar{position:absolute;left:14px;top:26px;width:68px;height:68px;border-radius:50%;background:linear-gradient(#c9b7a4,#8c7c6c)}
.quote-mark{position:absolute;left:94px;top:4px;font-family:Georgia,serif;font-size:40px;color:#ccc}
.quote-card p{position:absolute;left:112px;top:22px;width:186px;font-size:10.5px;line-height:20px;font-style:italic;color:#aaa}
.quote-card .author{position:absolute;left:100px;top:112px;font-size:12.5px;color:#333}
.t-dots{position:absolute;top:288px;left:0;width:100%;display:flex;justify-content:center;gap:4px}
.t-dots span{width:14px;height:14px;border-radius:50%;background:#999}
.t-dots span.on{background:var(--white);border:1px solid #999}

/* footer */
.site-footer{top:2871px;height:238px;background:var(--footer);color:var(--white)}
.f-col{position:absolute;top:46px}
.f-col h4{font-family:"Raleway",sans-serif;font-weight:500;font-size:16px;margin-bottom:12px}
.f-col li{list-style:none;font-size:12px;line-height:24px;color:rgba(255,255,255,.88)}
.f-col li svg{vertical-align:-2px;margin-right:5px}
.social{display:flex;gap:10px}
.social span{width:34px;height:34px;border-radius:50%;background:rgba(255,255,255,.45)}
.footer-bar{position:absolute;top:3109px;left:0;width:1200px;height:49px;background:var(--footer-bar);text-align:center;font-size:11px;line-height:49px;color:rgba(255,255,255,.85)}
</style>
</head>
<body>

<header class="site-header">
  <div class="brand"><span class="brand-dot"></span><span class="brand-name">NEXTWAY LABS</span></div>
</header>

<nav class="main-nav">
  <a class="active" href="#" style="width:127px">HOME</a>
  <a href="#" style="width:128px">ABOUT US</a>
  <a href="#" style="width:137px">SERVICES</a>
  <a href="#" style="width:128px">PROJECTS</a>
  <a href="#" style="width:160px">TECHNOLOGY</a>
  <a href="#" style="width:130px">OUR BLOG</a>
  <a href="#" style="width:130px;border-right:0">CONTACT</a>
</nav>

<section class="hero">
  <div class="hero-photo" role="img" aria-label="Aircraft climbing into a bright sunset sky"></div>
  <h1 class="hero-title">NEXT GENERATION TECHNOLOGY</h1>
  <p class="hero-sub">RESEARCH AND DEVELOPMENT</p>
  <span class="hero-arrow" style="left:170px"></span>
  <span class="hero-arrow" style="left:1000px"></span>
  <div class="hero-dots"><span class="on"></span><span></span><span></span><span></span></div>
</section>

<section class="about">
  <h2>ABOUT OUR COMPANY</h2>
  <p class="lead">Vivamus porttitor purus nisi eleifend libero a tempus libero lectus feugiat felis Morbi diam mauris viverra</p>
  <p class="body">consectetuer augue nisi quis lacus Ut ac mi quis lacus mollis aliquam Curabitur iaculis tempus eros Curabitur vel mi sit amet magna malesuada ultrices Ut nisi erat fermentum vel congue id euismod in elit Fusce ultricies orci ac feugiat suscipit leo massa sodales velit et scelerisque mi tortor at ipsum ligula augue bibendum accumsan vestibulum ut commodo a mi Morbi ornare gravida elit integer congue augue</p>
</section>

<section class="services" role="group" aria-label="Services">
  <div class="service" style="left:117px">
    <svg width="124" height="140" viewBox="0 0 124 140"><path d="M62 4a58 58 0 0 1 16 113.7L62 136 46 117.7A58 58 0 0 1 62 4z" fill="none" stroke="#fff" stroke-width="3"/><circle cx="62" cy="62" r="48" fill="var(--accent)" stroke="#fff" stroke-width="2"/><circle cx="62" cy="62" r="14" fill="none" stroke="#fff" stroke-width="6" stroke-dasharray="6 4"/><circle cx="62" cy="62" r="5" fill="#fff"/></svg>
    <h3>Research Services</h3>
    <p>Ut nisi erat fermentum vel congue id<br>euismod in elit Fusce ultricies orci ac<br>feugiat suscipit leo massa</p>
  </div>
  <div class="service" style="left:448px">
    <svg width="124" height="140" viewBox="0 0 124 140"><path d="M62 4a58 58 0 0 1 16 113.7L62 136 46 117.7A58 58 0 0 1 62 4z" fill="none" stroke="#fff" stroke-width="3"/><circle cx="62" cy="62" r="48" fill="var(--accent)" stroke="#fff" stroke-width="2"/><g fill="none" stroke="#fff" stroke-width="2.5"><circle cx="62" cy="62" r="20"/><ellipse cx="62" cy="62" rx="9" ry="20"/><line x1="42" y1="62" x2="82" y2="62"/></g></svg>
    <h3>Travel Development</h3>
    <p>Ut nisi erat fermentum vel congue id<br>euismod in elit Fusce ultricies orci ac<br>feugiat suscipit leo massa</p>
  </div>
  <div class="service" style="left:776px">
    <svg width="124" height="140" viewBox="0 0 124 140"><path d="M62 4a58 58 0 0 1 16 113.7L62 136 46 117.7A58 58 0 0 1 62 4z" fill="none" stroke="#fff" stroke-width="3"/><circle cx="62" cy="62" r="48" fill="var(--accent)" stroke="#fff" stroke-width="2"/><g fill="#fff"><circle cx="62" cy="56" r="9"/><path d="M44 82c2-12 10-16 18-16s16 4 18 16z"/><rect x="64" y="36" width="18" height="10" rx="3"/></g></svg>
    <h3>Consulting Service</h3>
    <p>Ut nisi erat fermentum vel congue id<br>euismod in elit Fusce ultricies orci ac<br>feugiat suscipit leo massa</p>
  </div>
</section>

<section class="what">
  <div class="what-media" role="img" aria-label="Laptop showing a world map with an aircraft in flight"></div>
  <div class="what-text">
    <h2>WHAT WE DO</h2>
    <p>Donec dictum lectus non odio Cras a ante vitae enim iaculis aliquam Mauris nunc quam venenatis nec euismod sit amet</p>
    <p>Morbi diam mauris viverra in gravida eu mattis in ante Morbi eget arcu Morbi porta libero id ullamcorper nonummy nibh ligula pulvinar metus eget consectetuer augue nisi quis lacus Ut ac mi quis lacus mollis aliquam Curabitur iaculis tempus eros Curabitur</p>
    <a class="btn btn-solid" href="#">READ MORE</a>
  </div>
</section>

<section class="tech">
  <div class="tech-panel">
    <h2>OUR TECHNOLOGY</h2>
    <p style="top:126px">Donec dictum lectus non odio Cras a ante vitae enim iaculis aliquam Mauris nunc quam venenatis nec euismod sit amet</p>
    <p style="top:182px">Morbi diam mauris viverra in gravida eu mattis in ante Morbi eget arcu Morbi porta libero id ullamcorper nonummy nibh ligula pulvinar metus eget consectetuer augue nisi quis lacus Ut ac mi quis lacus mollis aliquam Curabitur iaculis tempus eros Curabitur</p>
    <a class="btn btn-ghost" href="#">READ MORE</a>
  </div>
  <div class="tech-photo" role="img" aria-label="Business team reviewing documents and tablets together"></div>
</section>

<section class="projects">
  <h2 class="section-title">OUR PROJECTS</h2>
  <article class="project" style="left:126px">
    <div class="project-photo" role="img" aria-label="Professional working at a laptop"></div>
    <h3>Cum sociis natoque penati</h3>
    <p>tellus nec ultricies sit amet porttitor mattis enim in massa libero interdum ut nec interdum vel</p>
    <a href="#">READ MORE</a>
  </article>
  <article class="project" style="left:450px">
    <div class="project-photo" role="img" aria-label="Colleagues meeting around a table"></div>
    <h3>Donec convallis pede</h3>
    <p>tellus nec ultricies sit amet porttitor mattis enim in massa libero interdum ut nec interdum vel</p>
    <a href="#">READ MORE</a>
  </article>
  <article class="project" style="left:775px">
    <div class="project-photo" role="img" aria-label="Team collaborating at computers in an office"></div>
    <h3>Pellentesque rutrum</h3>
    <p>tellus nec ultricies sit amet porttitor mattis enim in massa libero interdum ut nec interdum vel</p>
    <a href="#">READ MORE</a>
  </article>
</section>

<section class="testimonials">
  <h2 class="section-title">TESTIMONIALS</h2>
  <div class="quote-card" style="left:124px">
    <div class="avatar" role="img" aria-label="Client portrait"></div>
    <span class="quote-mark">&ldquo;</span>
    <p>Class aptent taciti sociosqu ad litora torquent per conubia nostra per inceptos hymenaeos Proin nulla arcu nonummy luctus dictum</p>
    <span class="author">By Author Name</span>
  </div>
  <div class="quote-card" style="left:446px">
    <div class="avatar" role="img" aria-label="Client portrait"></div>
    <span class="quote-mark">&ldquo;</span>
    <p>Class aptent taciti sociosqu ad litora torquent per conubia nostra per inceptos hymenaeos Proin nulla arcu nonummy luctus dictum</p>
    <span class="author">By Author Name</span>
  </div>
  <div class="quote-card" style="left:766px">
    <div class="avatar" role="img" aria-label="Client portrait"></div>
    <span class="quote-mark">&ldquo;</span>
    <p>Class aptent taciti sociosqu ad litora torquent per conubia nostra per inceptos hymenaeos Proin nulla arcu nonummy luctus dictum</p>
    <span class="author">By Author Name</span>
  </div>
  <div class="t-dots"><span class="on"></span><span></span><span></span></div>
</section>

<footer class="site-footer">
  <div class="f-col" style="left:130px"><h4>ABOUT</h4><ul><li>Why Choose Us</li><li>How it Works</li><li>Our Team</li><li>Blogs</li></ul></div>
  <div class="f-col" style="left:305px"><h4>SERVICES</h4><ul><li>Travel Booking</li><li>Education</li><li>Find a Tour</li><li>Online Food</li></ul></div>
  <div class="f-col" style="left:488px"><h4>RESOURCES</h4><ul><li>Support</li><li>Testimonials</li><li>FAQ</li><li>Contact Us</li></ul></div>
  <div class="f-col" style="left:669px"><h4>CONTACT US</h4><ul>
    <li>Address: 120 Harbor Lane,</li>
    <li>Ridgefield, OR 97000</li>
    <li><svg width="12" height="12" viewBox="0 0 12 12"><path d="M3 1l2 3-1.3 1.3a7 7 0 0 0 3 3L8 7l3 2-1 2C5 11 1 7 1 2z" fill="#fff"/></svg>(07) 5550 1234</li>
    <li><svg width="12" height="10" viewBox="0 0 12 10"><rect x=".5" y=".5" width="11" height="9" fill="none" stroke="#fff"/><path d="M.5.5 6 5l5.5-4.5" fill="none" stroke="#fff"/></svg>hello@nextwaylabs.example</li>
  </ul></div>
  <div class="f-col" style="left:884px"><h4>FOLLOW US</h4><div class="social"><span></span><span></span><span></span><span></span></div></div>
</footer>
<div class="footer-bar">&copy; 2016 Company Name. All right reserved</div>

</body>
</html>
```